Current website re-design to a updated look and feel.

We currently have a website www.brightlanefreight.com that we want to give an updated look and feel to. We are a logistics company that competes with Pellwick, Dm Harrowgate, Quill but on a smaller scale. We want something fresh and updated. We have two locations one in downtown Chicago, IL and one in Palatine IL. We are a fun group that also gets the job done. We know we need pictures of both locations and possibly a video, but we need fresh design ideas. The 'who we are' page is really the only page that we currently want to keep. The 'what we do' page needs to be completely re-done from a look and feel for sure.

Target Market(s)

Anyone who uses Truck transportation to move their product. Mainly US manufacturers.

Industry/Entity Type

Logistics

Number of Pages Required

5+ page

Font styles to use
Sans Serif

Colors
5c91c4
0355a3
d0dfed

Requirements
Must have
• The new design must entice people to want to do business with us. The design must have locations for pictures and at least one video which we know we will have to provide. Design must be easy to navigate.

```html
<!DOCTYPE html>
<html lang="en">
<head>
<meta charset="utf-8">
<title>Brightlane Freight</title>
<link href="https://fonts.googleapis.com/css2?family=Marcellus&family=Open+Sans:wght@400;700;800&family=Roboto:wght@400;500;700&display=swap" rel="stylesheet">
<style>
:root{
  --brand:#0a79bf;
  --brand-dark:#0355a3;
  --brand-mid:#5c91c4;
  --brand-pale:#d0dfed;
  --footer:#2d95cf;
  --ink:#222;
  --body:#555;
  --white:#fff;
}
*{box-sizing:border-box;margin:0;padding:0}
html,body{width:1200px;height:2917px;overflow:hidden}
body{position:relative;background:var(--white);font-family:"Roboto",sans-serif;color:var(--body)}
.abs{position:absolute}

/* header */
.site-header{left:0;top:0;width:1200px;height:93px;background:var(--white);box-shadow:0 2px 6px rgba(0,0,0,.12);z-index:2}
.brand{left:78px;top:18px;display:flex;align-items:center;gap:12px;font-family:"Roboto",sans-serif;font-weight:500;font-size:34px;color:var(--brand-dark);letter-spacing:-.5px}
.brand-dot{width:18px;height:18px;border-radius:50%;background:var(--brand-dark)}
.main-nav{top:34px;left:0;width:1200px}
.main-nav a{position:absolute;font-size:20px;color:var(--brand);text-decoration:none;white-space:nowrap}
.main-nav a.active{color:var(--ink);border-bottom:2px solid var(--brand);padding:0 14px 12px;margin-left:-14px}

/* hero */
.hero{left:0;top:93px;width:1200px;height:574px;background:linear-gradient(180deg,#2f76c9 0%,#8bb8e2 38%,#dfe9ef 52%,#7fa75b 60%,#4d4f50 70%,#3b3d3e 100%)}
.hero-title{left:78px;top:252px;font-family:"Open Sans",sans-serif;font-weight:800;font-size:62px;line-height:1;color:#111}
.hero-sub{left:78px;top:320px;font-family:"Open Sans",sans-serif;font-weight:800;font-size:43px;line-height:1;color:#111}
.hero-text{left:78px;top:370px;width:400px;font-size:20px;line-height:26px;color:#111}
.btn{display:flex;align-items:center;justify-content:center;border-radius:30px;font-size:19px;text-transform:uppercase;text-decoration:none}
.btn-light{left:78px;top:453px;width:187px;height:51px;background:var(--white);color:#111}
.slider-dots{left:556px;top:630px;display:flex;gap:10px}
.slider-dots span{width:21px;height:21px;border-radius:50%;background:var(--white)}
.slider-dots span.on{background:var(--brand-dark);border:2px solid var(--white)}

/* sections */
.section-title{left:0;width:1200px;text-align:center;font-family:"Marcellus",serif;font-size:33px;color:var(--ink);letter-spacing:1px}
.lede{left:130px;width:940px;text-align:center;font-size:14px;line-height:21px;color:var(--body)}
.btn-brand{left:506px;top:856px;width:186px;height:51px;background:var(--brand);color:var(--white)}

.services{left:0;top:963px;width:1200px;height:1163px;background:linear-gradient(180deg,#5a5a5a 0%,#8c8c8a 35%,#6e6e6c 70%,#4b4b4b 100%)}
.services-title{top:1013px;color:var(--white)}
.service-photo{width:208px;height:266px;border:3px solid var(--white)}
.service-card{width:407px;height:208px;background:var(--white);padding:28px 34px 0 48px;box-shadow:0 4px 14px rgba(0,0,0,.35)}
.service-card h3{font-family:"Marcellus",serif;font-weight:400;font-size:25px;color:var(--brand);margin-bottom:12px}
.service-card p{font-size:14px;line-height:22px;color:var(--body)}
.service-card a{display:inline-block;margin-top:14px;font-family:"Marcellus",serif;font-size:17px;color:var(--brand);letter-spacing:.5px}

.mission h3{position:absolute;left:0;width:1200px;text-align:center;font-size:19px;font-weight:700;color:#444;text-decoration:underline}

/* footer */
.site-footer{left:0;top:2495px;width:1200px;height:422px;background:linear-gradient(180deg,#2a93d0 0%,#3aa0d8 55%,#2f8ec7 100%)}
.foot-brand{left:78px;top:2545px;font-family:"Roboto",sans-serif;font-weight:500;font-size:32px;color:var(--white)}
.foot-text{left:78px;top:2620px;width:300px;font-size:15px;line-height:21px;color:var(--white)}
.foot-head{font-family:"Marcellus",serif;font-size:18px;color:var(--white)}
.contact-item{left:438px;display:flex;gap:14px;font-size:15px;line-height:21px;color:var(--white)}
.contact-item svg{flex:none;margin-top:2px}
.field{border:1.5px solid rgba(255,255,255,.85);color:var(--white);font-size:15px;padding:12px 10px}
.btn-submit{left:846px;top:2779px;width:185px;height:53px;background:var(--white);color:var(--brand);font-size:19px}
.foot-rule{left:78px;top:2871px;width:1044px;height:1px;background:rgba(255,255,255,.5)}
.copyright{left:0;top:2885px;width:1200px;text-align:center;font-size:14px;color:var(--white)}
.copyright b{color:#111;font-weight:500}
</style>
</head>
<body>

<header class="site-header abs">
  <div class="brand abs"><span class="brand-dot"></span>Brightlane Freight</div>
  <nav class="main-nav abs">
    <a class="active" style="left:518px" href="#">Home</a>
    <a style="left:602px" href="#">What We Do</a>
    <a style="left:752px" href="#">Who We Are</a>
    <a style="left:903px" href="#">Tracking</a>
    <a style="left:1025px" href="#">Contact Us</a>
  </nav>
</header>

<section class="hero abs" role="img" aria-label="Photo of a white truck with green trailer on a highway under a blue sky"></section>
<h1 class="hero-title abs">RELEX.</h1>
<div class="hero-sub abs">WE GOT THIS.</div>
<p class="hero-text abs">We provide friendly, exceptional service that makes it easy to do business with us. Give us a call today !</p>
<a class="btn btn-light abs" href="#">Call us now</a>
<div class="slider-dots abs"><span></span><span class="on"></span><span></span></div>

<h2 class="section-title abs" style="top:715px">WHO WE ARE</h2>
<p class="lede abs" style="top:773px">Brightlane Freight welcomes you to our growing family of clients! We have over 26 years of experience in helping people solve their logistics needs from coast-to-coast. We also provide friendly, exceptional service that makes it easy to do business with us. Give us a call today and experience the difference for yourself!</p>
<a class="btn btn-brand abs" href="#">Read more</a>

<section class="services abs" role="img" aria-label="Photo of a warehouse interior stacked with white sacks"></section>
<h2 class="section-title services-title abs">WHAT WE DO</h2>

<div class="service-card abs" style="left:286px;top:1089px">
  <h3>Freight Management</h3>
  <p>We strive for a perfect delivery and promise to be there for anything you may need, every step of the way.</p>
  <a href="#">READ MORE</a>
</div>
<div class="service-photo abs" style="left:78px;top:1070px;background:linear-gradient(180deg,#6fa8d8,#4a8fb8 55%,#7a6a58)" role="img" aria-label="Photo of a container ship at sea"></div>

<div class="service-card abs" style="left:506px;top:1334px">
  <h3>Transportation</h3>
  <p>With a combined 500+ years of industry experience between all employees, we are the logistics company you need to get the job done.</p>
  <a href="#">READ MORE</a>
</div>
<div class="service-photo abs" style="left:914px;top:1315px;background:linear-gradient(180deg,#2a3448,#c86a3a 40%,#4a3a3c 60%,#8a2a2a)" role="img" aria-label="Photo of highway light trails at dusk"></div>

<div class="service-card abs" style="left:286px;top:1585px">
  <h3>Warehouse &amp; Distribution</h3>
  <p>Our secure facility can accommodate large or small quantities of product. Our inventory management system provides real-time visibility.</p>
  <a href="#">READ MORE</a>
</div>
<div class="service-photo abs" style="left:78px;top:1566px;background:linear-gradient(180deg,#7a6a50,#c9b48a 45%,#8a6a42)" role="img" aria-label="Photo of a warehouse aisle with stacked boxes"></div>

<div class="service-card abs" style="left:506px;top:1830px">
  <h3>Carriers</h3>
  <p>Are you a carrier looking to work with Brightlane? Click here to find out why we have the best carrier relationships in the business.</p>
  <a href="#">READ MORE</a>
</div>
<div class="service-photo abs" style="left:914px;top:1811px;background:linear-gradient(180deg,#d79a7a,#8a6aa8 45%,#3a3a6a 75%,#4a4448)" role="img" aria-label="Photo of a truck driving at sunset"></div>

<section class="mission">
  <h2 class="section-title abs" style="top:2178px">MISSION AND VISION</h2>
  <h3 style="top:2234px">Brightlane Mission</h3>
  <p class="lede abs" style="top:2264px">Brightlane's mission is to provide the most thorough and satisfying third-party logistics experience for its customers. Brightlane uses leading technologies and an industry experienced staff to deliver an unparalleled customer service experience. Brightlane leverages the most efficient mode of transportation, and tailors cost effective solutions for warehousing and distribution of your products in every situation.</p>
  <h3 style="top:2350px">Brightlane Vision</h3>
  <p class="lede abs" style="top:2382px">Brightlane vision is to be the premier third party logistics solution in North America. We will become premier by providing superior customer service, efficient and cost effective warehousing and distribution solutions. The decisions we make today for hiring, training, technology, strategic services and customer satisfaction are based on this vision.</p>
</section>

<footer class="site-footer abs" role="img" aria-label="Faint photo of a city skyline and harbour cranes tinted blue"></footer>
<div class="foot-brand abs">Brightlane Freight</div>
<p class="foot-text abs">Brightlane Freight welcomes you to our growing family of clients! We provide friendly, exceptional service that makes it easy to do business with us!</p>

<div class="foot-head abs" style="left:438px;top:2548px">Contact Us</div>
<div class="contact-item abs" style="top:2600px">
  <svg width="14" height="20" viewBox="0 0 14 20"><path d="M7 0a7 7 0 0 0-7 7c0 5 7 13 7 13s7-8 7-13a7 7 0 0 0-7-7zm0 9.5A2.5 2.5 0 1 1 7 4.5a2.5 2.5 0 0 1 0 5z" fill="#fff"/></svg>
  <div>418 W Orchard Ave Suite 210<br>Cedarbrook, MN 55390</div>
</div>
<div class="contact-item abs" style="top:2668px">
  <svg width="16" height="16" viewBox="0 0 24 24"><path d="M6.6 10.8a15 15 0 0 0 6.6 6.6l2.2-2.2c.3-.3.7-.4 1-.2 1.1.4 2.3.6 3.6.6.6 0 1 .4 1 1V20c0 .6-.4 1-1 1A17 17 0 0 1 3 4c0-.6.4-1 1-1h3.5c.6 0 1 .4 1 1 0 1.3.2 2.5.6 3.6.1.3 0 .7-.2 1z" fill="#fff"/></svg>
  <div>320.555.0140<br>320.555.0142</div>
</div>
<div class="contact-item abs" style="top:2733px">
  <svg width="16" height="13" viewBox="0 0 16 13"><rect width="16" height="13" rx="1" fill="#fff"/><path d="M1 1l7 6 7-6" stroke="#2d95cf" stroke-width="1.5" fill="none"/></svg>
  <div>info@brightlanefreight.com</div>
</div>

<div class="foot-head abs" style="left:757px;top:2548px">Get In Touch</div>
<div class="field abs" style="left:755px;top:2598px;width:180px;height:47px">Name</div>
<div class="field abs" style="left:943px;top:2598px;width:179px;height:47px">Contact No.</div>
<div class="field abs" style="left:755px;top:2649px;width:367px;height:47px">E mail ID</div>
<div class="field abs" style="left:755px;top:2702px;width:367px;height:68px">Message...</div>
<a class="btn btn-submit abs" href="#">Submit</a>

<div class="foot-rule abs"></div>
<p class="copyright abs">Copyright © 2017 <b>Brightlane Freight</b>. All rights reserved.</p>

</body>
</html>
```